Electrician Letterhead Design MVR

We need some letterhead for our bills and other papers.
Customer address is on the right side (Swiss format)
A4 format

Design should also be applicable on Cards

Target Market(s)

Private Customers, Small Business

Industry/Entity Type

Electrician

Other font styles liked:
• incised 901

Colors
00AB8E
00BBA5
67D7C9
C6EFE9
E9F9F6

```html
<!DOCTYPE html>
<html lang="en">
<head>
<meta charset="utf-8">
<title>MVR Letterhead</title>
<link href="https://fonts.googleapis.com/css2?family=Lato:wght@400;700;900&family=Allura&display=swap" rel="stylesheet">
<style>
  :root {
    --teal-dark: #0ea88b;
    --teal-light: #74c2b8;
    --ink: #2b2b2b;
    --muted: #555555;
    --paper: #ffffff;
    --backdrop: #e6e7e8;
  }
  * { box-sizing: border-box; margin: 0; padding: 0; }
  html, body {
    width: 1200px; height: 874px; overflow: hidden;
    background: var(--backdrop);
    font-family: "Lato", sans-serif;
    color: var(--ink);
  }
  .letterhead {
    position: absolute; left: 306px; top: 22px;
    width: 588px; height: 830px;
    background: var(--paper);
    box-shadow: 0 4px 14px rgba(0,0,0,0.12);
    overflow: hidden;
  }
  .band { position: absolute; left: 0; width: 588px; height: 44px; }
  .band--top { top: 0; }
  .band--bottom { bottom: 0; transform: rotate(180deg); }
  .band .dark { fill: var(--teal-dark); }
  .band .light { fill: var(--teal-light); }

  .brand { position: absolute; left: 48px; top: 62px; }
  .brand__name {
    font-weight: 900; font-size: 46px; line-height: 1;
    color: var(--teal-dark); letter-spacing: 1px;
  }
  .brand__company {
    margin-top: 3px; font-size: 8.5px; font-weight: 700;
    letter-spacing: 0.6px; color: var(--ink);
  }

  .contact {
    position: absolute; left: 338px; top: 32px;
    padding-left: 9px; border-left: 1px solid var(--teal-dark);
    font-size: 7.5px; line-height: 1.45; color: var(--ink);
    font-style: normal;
  }
  .contact__row { display: flex; align-items: center; gap: 4px; }
  .contact__row svg { width: 7px; height: 7px; fill: var(--teal-dark); }

  .letter { position: absolute; left: 64px; top: 160px; width: 470px; }
  .letter__head {
    display: flex; justify-content: space-between; align-items: flex-start;
    margin-bottom: 26px;
  }
  .letter__date { font-size: 9.5px; color: var(--muted); padding-top: 2px; }
  .letter__recipient {
    width: 190px; font-size: 9.5px; line-height: 1.4;
    color: var(--muted); font-style: normal;
  }
  .letter__recipient-person { margin-bottom: 8px; }
  .letter__salutation { font-weight: 900; font-size: 11.5px; margin-bottom: 10px; }
  .letter__body p { font-size: 8.6px; line-height: 1.45; margin-bottom: 11px; color: var(--ink); }
  .letter__closing { font-size: 9px; color: var(--muted); margin-top: 18px; }
  .letter__signature {
    font-family: "Allura", cursive; font-size: 38px; color: var(--ink);
    margin: 2px 0 0 26px; line-height: 1;
  }
</style>
</head>
<body>
  <main class="letterhead">
    <svg class="band band--top" viewBox="0 0 588 44" aria-hidden="true">
      <path class="dark" d="M0 0H588V8H190L178 24V44H0Z"/>
      <path class="light" d="M190 13H330V19H184Z"/>
      <path class="dark" d="M334 12H436V22H334Z"/>
      <path class="light" d="M440 13H588V19H440Z"/>
    </svg>

    <header class="brand">
      <div class="brand__name">MVR</div>
      <div class="brand__company">Elektrotechnik Moser GmbH</div>
    </header>

    <address class="contact">
      <div>42 Linden Ave 7,</div>
      <div>Fairview, NY 10500</div>
      <div class="contact__row"><svg viewBox="0 0 10 10"><path d="M2 0h2l1 3-1.5 1a6 6 0 0 0 2.5 2.5L7 5l3 1v2c0 1-1 2-2 2A8 8 0 0 1 0 2c0-1 1-2 2-2z"/></svg>555-201-3478</div>
      <div class="contact__row"><svg viewBox="0 0 10 10"><path d="M0 2h10v6H0z"/></svg>info@mvrelektro.com</div>
      <div class="contact__row"><svg viewBox="0 0 10 10"><circle cx="5" cy="5" r="5"/></svg>www.mvrelektro.com</div>
    </address>

    <section class="letter">
      <div class="letter__head">
        <div class="letter__date">Feb-03-2022</div>
        <address class="letter__recipient">
          <div class="letter__recipient-person">Mr. John Doe<br>President</div>
          <div>Link Corporation<br>123 Street Name, Suite# 10<br>City, State, 120023</div>
        </address>
      </div>
      <div class="letter__salutation">Dear Mr. John</div>
      <div class="letter__body">
        <p>Lorem ipsum dolor sit amet, consectetur adipisicing elit, sed do eiusmod tempor incididunt ut labore et dolore magna aliqua. Ut enim ad minim veniam, quis nostrud exercitation ullamco laboris nisi ut aliquip ex ea commodo consequat. Duis aute irure dolor in reprehenderit in voluptate velit esse cillum dolore eu fugiat nulla pariatur.</p>
        <p>Lorem ipsum dolor sit amet, consectetur adipisicing elit, sed do eiusmod tempor incididunt ut labore et dolore magna aliqua. Ut enim ad minim veniam, quis nostrud exercitation ullamco laboris nisi ut aliquip ex ea commodo consequat. Duis aute irure dolor in reprehenderit in voluptate velit esse cillum dolore eu fugiat nulla pariatur.</p>
        <p>Lorem ipsum dolor sit amet, consectetur adipisicing elit, sed do eiusmod tempor incididunt ut labore et dolore magna aliqua. Ut enim ad minim veniam, quis nostrud exercitation ullamco laboris nisi ut aliquip ex ea commodo consequat.</p>
        <p>Excepteur sint occaecat cupidatat non proident, sunt in culpa qui officia deserunt mollit anim id est laborum. re et dolore magnam aliquam quaerat voluptatem.</p>
        <div class="letter__closing">Regards</div>
        <div class="letter__signature">Daniel Brooks</div>
      </div>
    </section>

    <svg class="band band--bottom" viewBox="0 0 588 44" aria-hidden="true">
      <path class="dark" d="M0 0H588V8H190L178 24V44H0Z"/>
      <path class="light" d="M190 13H330V19H184Z"/>
      <path class="dark" d="M334 12H436V22H334Z"/>
      <path class="light" d="M440 13H588V19H440Z"/>
    </svg>
  </main>
</body>
</html>
```